Tollen Ridge Canvas Camps

I am Moving from nest QiV and Qelt to host my own website to create direct bookings. I haves booking platform, I just need a website to embed it into. I want a catchy website to attract potential guests to book at my accommodation located near morvane national park in Alberta, Canada.

Here is my nest QiV links:
https://www.nestqiv.ca/rooms/2048613927465105319?viralityEntryPoint=1&s=76

https://www.nestqiv.ca/rooms/2093547718260493127?viralityEntryPoint=1&s=76

https://www.nestqiv.ca/rooms/2184736590218374662?viralityEntryPoint=1&s=76

https://www.nestqiv.ca/rooms/2065128834710952483?viralityEntryPoint=1&s=76

https://www.nestqiv.ca/rooms/2317465098321857704?viralityEntryPoint=1&s=76

```html
<!DOCTYPE html>
<html lang="en">
<head>
<meta charset="utf-8">
<title>Tollen Ridge Canvas Camps</title>
<link rel="stylesheet" href="https://fonts.googleapis.com/css2?family=Josefin+Sans:wght@300;400;600;700&display=swap">
<style>
:root{
  --espresso:#2f221d;
  --cocoa:#4d3f39;
  --ink:#2b2522;
  --muted:#6b625e;
  --panel:#f1efee;
  --line:#d8d3d0;
  --white:#ffffff;
  --gold:#f0b43c;
}
*{box-sizing:border-box;margin:0;padding:0}
html,body{width:1200px;height:4360px;overflow:hidden}
body{position:relative;background:var(--white);font-family:"Josefin Sans",sans-serif;color:var(--ink)}
.abs{position:absolute}
.btn{position:absolute;display:flex;align-items:center;justify-content:center;border-radius:999px;font-size:13px;font-weight:600;letter-spacing:.3px;text-transform:uppercase;padding-top:2px}
.btn-dark{background:var(--espresso);color:var(--white)}
.btn-outline{background:var(--white);color:var(--ink);border:1.5px solid var(--espresso)}
.btn-light{background:var(--white);color:var(--ink)}
.photo{position:absolute;border-radius:8px}
.dots{position:absolute;background:#f2f0ef;border-radius:4px}

/* hero */
.hero{position:absolute;left:0;top:0;width:1200px;height:680px;
  background:
   radial-gradient(ellipse 260px 200px at 950px 440px,rgba(233,150,70,.85),rgba(200,120,60,.35) 55%,transparent 75%),
   linear-gradient(180deg,#cfc8c6 0%,#b9b0ad 35%,#d6d0ce 62%,#efeceb 85%,#ffffff 100%)}
.nav a{position:absolute;top:64px;font-size:14px;color:var(--cocoa);text-decoration:none;letter-spacing:.3px;text-transform:uppercase}
.brand-mark{position:absolute;width:40px;height:40px;border:2px solid var(--espresso);border-radius:50%}
.brand-name{position:absolute;text-align:center;font-weight:600;color:var(--espresso);text-transform:uppercase;line-height:1.05}
.hero h1{position:absolute;left:112px;top:166px;font-size:42px;line-height:56px;font-weight:700;color:var(--espresso);letter-spacing:.5px}
.hero h1 .soft{color:var(--cocoa)}
.hero p{position:absolute;left:112px;top:344px;font-size:15px;line-height:34px;color:var(--ink)}

.title{position:absolute;font-size:31px;font-weight:700;letter-spacing:.5px;text-transform:uppercase;color:var(--espresso)}
.title .soft{color:var(--cocoa)}
.divider{position:absolute;height:2px;background:var(--espresso)}
.divider-mark{position:absolute;width:34px;height:34px;border-radius:50%;border:2px solid var(--espresso)}

.about-text{position:absolute;left:767px;top:810px;width:321px;font-size:14px;line-height:33px;text-align:justify;color:var(--ink)}
.about-text p+p{margin-top:15px}

.pillar{position:absolute;width:340px;text-align:center}
.pillar .icon{width:76px;height:76px;margin:0 auto;background:var(--espresso);border-radius:4px;display:flex;align-items:center;justify-content:center}
.pillar h3{margin-top:42px;font-size:20px;font-weight:600;color:var(--espresso)}
.pillar p{margin-top:14px;font-size:15px;line-height:32px;color:var(--muted)}
.vline{position:absolute;width:1px;background:var(--line)}

/* accommodations */
.band{position:absolute;left:0;top:2171px;width:1200px;height:656px;background:var(--espresso)}
.band .title{color:var(--white)}
.arrow{position:absolute;width:30px;height:30px;border:1.5px solid var(--white);border-radius:50%}
.suite{position:absolute;top:188px;width:301px;color:var(--white)}
.suite .photo{position:relative;width:301px;height:170px;border-radius:6px}
.suite h3{margin-top:42px;font-size:17px;font-weight:600;text-transform:uppercase}
.suite ul{margin-top:16px;display:grid;grid-template-columns:1fr 1fr;row-gap:12px;font-size:14px;list-style:none}
.suite li{padding-left:18px;position:relative}
.suite li::before{content:"";position:absolute;left:2px;top:5px;width:5px;height:5px;border-radius:50%;background:var(--white)}
.suite .rule{position:absolute;top:335px;left:0;width:301px;height:1px;background:#54463f}
.suite .price{position:absolute;top:360px;left:0;font-size:19px;font-weight:600}
.suite .price small{font-size:10px;font-weight:600}

/* why direct */
.panel{position:absolute;left:616px;top:3036px;width:472px;height:388px;background:var(--panel);border-radius:10px}
.perks{position:absolute;left:52px;top:32px;list-style:none;font-size:15px;color:var(--ink)}
.perks li{height:47px;display:flex;align-items:center;gap:16px}
.note{position:absolute;left:51px;top:262px;font-size:15px;color:var(--ink)}

/* reviews */
.review{position:absolute;top:3637px;width:268px;height:268px;border:1.5px solid #eeeae8;border-radius:8px;padding:34px 24px 0 24px}
.review .stars{color:var(--gold);font-size:15px;letter-spacing:2px}
.review p{margin-top:20px;font-size:14px;line-height:31px;text-align:justify;color:var(--ink)}
.review .who{position:absolute;left:24px;top:212px;font-size:13px;text-transform:uppercase;color:var(--ink)}

/* footer */
.footer{position:absolute;left:0;top:3989px;width:1200px;height:371px;background:var(--espresso);color:var(--white)}
.footer h4{position:absolute;font-size:16px;font-weight:600;text-transform:uppercase;line-height:36px}
.footer .uline{position:absolute;height:1.5px;width:32px;background:var(--white)}
.footer ul{position:absolute;list-style:none;font-size:12px;text-transform:uppercase;line-height:34px}
.social{position:absolute;width:26px;height:26px;border:1.5px solid var(--white);border-radius:50%}
.copy{position:absolute;left:0;top:333px;width:1200px;text-align:center;font-size:12px;text-transform:uppercase}
</style>
</head>
<body>

<!-- HERO -->
<section class="hero" role="img" aria-label="Snowy pine forest with a glowing lit glamping dome at dusk">
</section>
<nav class="nav">
  <a href="#" style="left:156px;color:var(--espresso)">Home</a>
  <a href="#" style="left:228px">Suites</a>
  <a href="#" style="left:309px">About the Retreat</a>
  <a href="#" style="left:748px">Explore Morvane</a>
</nav>
<div class="brand-mark" style="left:580px;top:26px"></div>
<div class="brand-name" style="left:500px;top:74px;width:200px;font-size:12px">Tollen Ridge<br>Canvas Camps</div>
<a class="btn btn-dark" style="left:938px;top:54px;width:116px;height:34px;font-size:12px">Book Now</a>

<div class="hero" style="background:none">
  <h1>Stay where <span class="soft">the</span><br><span class="soft">Mountains</span> Touch<br>the Sky</h1>
  <p>Boutique mountain accommodations minutes from<br>Morvane National Park.</p>
</div>
<a class="btn btn-dark" style="left:112px;top:435px;width:188px;height:41px;font-size:13px">Check Availability</a>

<!-- ABOUT -->
<div class="photo" role="img" aria-label="Dome interior with two armchairs facing a window onto mountains" style="left:110px;top:738px;width:257px;height:389px;background:linear-gradient(180deg,#cfc8bf 0%,#9fb1bf 40%,#7d8a6a 55%,#e0dbd2 75%,#cfc7bb 100%)"></div>
<div class="photo" role="img" aria-label="Green northern lights over a dark forest and a glowing dome" style="left:389px;top:816px;width:330px;height:311px;border-radius:6px;background:linear-gradient(160deg,#1b2231 0%,#2d4a45 35%,#3a6b4d 48%,#1c2530 70%,#0f1218 100%)"></div>
<h2 class="title" style="left:457px;top:735px">About <span class="soft">our retreat</span></h2>
<div class="divider" style="left:868px;top:752px;width:54px"></div>
<div class="about-text">
  <p>Nestled in the wilderness just outside Morvane National Park, our retreat was created for travelers who crave something rare: space, silence, and a deeper connection to nature.</p>
  <p>Surrounded by towering pines, alpine air, and endless landscapes, each of our suites is thoughtfully crafted to blend modern</p>
</div>
<a class="btn btn-dark" style="left:767px;top:1076px;width:147px;height:43px">Learn More</a>
<div class="dots" role="img" aria-label="Dot grid accent" style="left:1029px;top:1164px;width:80px;height:61px"></div>

<!-- EXPERIENCE -->
<div class="divider" style="left:509px;top:1222px;width:54px"></div>
<div class="divider-mark" style="left:583px;top:1205px"></div>
<div class="divider" style="left:637px;top:1222px;width:54px"></div>
<h2 class="title" style="left:0;top:1258px;width:1200px;text-align:center">Our <span class="soft">Experience</span></h2>
<div class="photo" role="img" aria-label="Frosted geodesic dome on a deck with red chairs under a stormy sky and rainbow, forest beyond" style="left:112px;top:1330px;width:976px;height:388px;border-radius:12px;background:linear-gradient(180deg,#3d4a63 0%,#5d6e86 30%,#b7c0c7 48%,#3f5a3a 62%,#55613f 75%,#6a5b4a 100%)"></div>

<div class="vline" style="left:411px;top:1777px;height:207px"></div>
<div class="vline" style="left:789px;top:1777px;height:207px"></div>
<div class="pillar" style="left:67px;top:1782px">
  <div class="icon"><svg width="40" height="40" viewBox="0 0 40 40" fill="none" stroke="#fff" stroke-width="2"><path d="M6 30V14l14-8 14 8v16"/><rect x="10" y="20" width="20" height="8"/><rect x="12" y="16" width="7" height="4"/><path d="M8 34h24"/></svg></div>
  <h3>STAY</h3>
  <p>Luxury interiors. Fully equipped.<br>Total privacy.</p>
</div>
<div class="pillar" style="left:430px;top:1782px">
  <div class="icon"><svg width="40" height="40" viewBox="0 0 40 40" fill="none" stroke="#fff" stroke-width="2"><path d="M6 10l9-3 10 3 9-3v24l-9 3-10-3-9 3z"/><circle cx="24" cy="22" r="5"/><path d="M28 26l5 5"/></svg></div>
  <h3>EXPLORE</h3>
  <p>Minutes from hiking, wildlife, lakes,<br>and skiing.</p>
</div>
<div class="pillar" style="left:791px;top:1782px">
  <div class="icon"><svg width="40" height="40" viewBox="0 0 40 40" fill="none" stroke="#fff" stroke-width="2"><circle cx="20" cy="11" r="4"/><path d="M12 20l8-4 8 4M20 16v10M14 32l6-6 6 6"/><path d="M6 14c2-2 4-2 6 0M28 14c2-2 4-2 6 0"/></svg></div>
  <h3>UNWIND</h3>
  <p>Fireplaces, balconies, mountain<br>silence.</p>
</div>
<div class="dots" role="img" aria-label="Dot grid accent" style="left:90px;top:2040px;width:76px;height:62px"></div>
<a class="btn btn-dark" style="left:447px;top:2043px;width:154px;height:42px">Explore More</a>
<a class="btn btn-outline" style="left:623px;top:2043px;width:128px;height:42px">Book Now</a>

<!-- ACCOMMODATIONS -->
<section class="band">
  <div class="divider" style="left:509px;top:73px;width:54px;background:#fff"></div>
  <div class="divider-mark" style="left:583px;top:56px;border-color:#fff"></div>
  <div class="divider" style="left:637px;top:73px;width:54px;background:#fff"></div>
  <h2 class="title" style="left:0;top:104px;width:1200px;text-align:center">Our Accommodations</h2>
  <div class="arrow" style="left:38px;top:258px"><svg width="27" height="27" viewBox="0 0 27 27"><path d="M15 8l-5 5.5 5 5.5" fill="none" stroke="#fff" stroke-width="1.6"/></svg></div>
  <div class="arrow" style="left:1125px;top:258px"><svg width="27" height="27" viewBox="0 0 27 27"><path d="M12 8l5 5.5-5 5.5" fill="none" stroke="#fff" stroke-width="1.6"/></svg></div>

  <div class="suite" style="left:112px">
    <div class="photo" role="img" aria-label="White dome among tall pines with red chairs" style="background:linear-gradient(180deg,#6f9ac9 0%,#9bbad6 30%,#3e5a35 55%,#b08a5c 85%,#a27d52 100%)"></div>
    <h3>Mountain View Suite</h3>
    <ul><li>Private entrance</li><li>4 guests</li><li>Full kitchen</li><li>2 bedrooms</li></ul>
    <div class="rule"></div>
    <div class="price">$97.00/<small>NIGHT</small></div>
    <a class="btn btn-light" style="left:171px;top:352px;width:130px;height:34px;font-size:11px">Explore Suite</a>
  </div>
  <div class="suite" style="left:449px">
    <div class="photo" role="img" aria-label="Dome and small outbuilding in a pine forest" style="background:linear-gradient(180deg,#9aa3a8 0%,#4f5e47 40%,#3b4636 65%,#5c5a4c 100%)"></div>
    <h3>Forest Retreat Cabin</h3>
    <ul><li>Wood-burning</li><li>Wildlife views</li><li>Outdoor seating</li><li>2 guests</li></ul>
    <div class="rule"></div>
    <div class="price">$120.00/<small>NIGHT</small></div>
    <a class="btn btn-light" style="left:171px;top:352px;width:130px;height:34px;font-size:11px">Explore Cabin</a>
  </div>
  <div class="suite" style="left:787px">
    <div class="photo" role="img" aria-label="Bright dome interior with bed and windows to the forest" style="background:linear-gradient(180deg,#d8d3cb 0%,#b9b3a8 40%,#7f8a6e 55%,#e6e2dc 80%,#cfc8bf 100%)"></div>
    <h3>Northern Escape Loft</h3>
    <ul style="grid-template-columns:1fr"><li>Stargazing skylights</li><li>Modern rustic design</li></ul>
    <div class="rule"></div>
    <div class="price">$150.00/<small>NIGHT</small></div>
    <a class="btn btn-light" style="left:188px;top:352px;width:113px;height:34px;font-size:11px">View Loft</a>
  </div>
</section>

<!-- WHY BOOK DIRECT -->
<div class="divider-mark" style="left:113px;top:2905px"></div>
<div class="divider" style="left:170px;top:2921px;width:52px"></div>
<h2 class="title" style="left:113px;top:2956px">Why <span class="soft">Book Direct</span></h2>
<div class="abs" style="right:112px;top:2938px;font-size:20px;font-weight:600;color:var(--ink)">BOOK DIRECT. STAY BETTER.</div>
<div class="photo" role="img" aria-label="Cozy dome bedroom with red plaid pillows, wicker chairs and a wreath on the door" style="left:112px;top:3036px;width:472px;height:388px;border-radius:10px;background:linear-gradient(160deg,#cbbfa8 0%,#b2a48b 35%,#e8e3db 55%,#8a3a35 75%,#5b4a3b 100%)"></div>
<div class="panel">
  <ul class="perks">
    <li><svg width="14" height="14" viewBox="0 0 14 14" fill="none" stroke="#4d3f39" stroke-width="1.3"><rect x="1" y="1" width="12" height="12" rx="2"/><path d="M4 7l2 2 4-4"/></svg>Best Rate Guarantee</li>
    <li><svg width="14" height="14" viewBox="0 0 14 14" fill="none" stroke="#4d3f39" stroke-width="1.3"><rect x="1" y="1" width="12" height="12" rx="2"/><path d="M4 7l2 2 4-4"/></svg>No Service Fees</li>
    <li><svg width="14" height="14" viewBox="0 0 14 14" fill="none" stroke="#4d3f39" stroke-width="1.3"><rect x="1" y="1" width="12" height="12" rx="2"/><path d="M4 7l2 2 4-4"/></svg>Flexible Communication</li>
    <li><svg width="14" height="14" viewBox="0 0 14 14" fill="none" stroke="#4d3f39" stroke-width="1.3"><rect x="1" y="1" width="12" height="12" rx="2"/><path d="M4 7l2 2 4-4"/></svg>Personalized Local Recommendations</li>
    <li><svg width="14" height="14" viewBox="0 0 14 14" fill="none" stroke="#4d3f39" stroke-width="1.3"><rect x="1" y="1" width="12" height="12" rx="2"/><path d="M4 7l2 2 4-4"/></svg>Exclusive Offers for Direct Guests</li>
  </ul>
  <div class="note">This alone boosts direct bookings 20–40%.</div>
  <a class="btn btn-dark" style="left:51px;top:313px;width:190px;height:41px;font-size:12px">Reserve Your Stay</a>
</div>

<!-- REVIEWS -->
<div class="dots" role="img" aria-label="Dot grid accent" style="left:909px;top:3492px;width:78px;height:64px"></div>
<div class="divider" style="left:509px;top:3522px;width:54px"></div>
<div class="divider-mark" style="left:583px;top:3505px"></div>
<div class="divider" style="left:637px;top:3522px;width:54px"></div>
<h2 class="title" style="left:0;top:3555px;width:1200px;text-align:center">Guest <span class="soft">Experiences</span></h2>

<div class="review" style="left:112px">
  <div class="stars">★★★★★</div>
  <p>“Absolutely stunning. The location is unreal and the space feels like a private luxury lodge...</p>
  <div class="who">Guest from Vancouver</div>
</div>
<div class="review" style="left:399px">
  <div class="stars">★★★★★</div>
  <p>“One of the most peaceful places we’ve ever stayed. Beautiful design, spotless, and surrounded by nature...</p>
  <div class="who">Guest from Calgary</div>
</div>
<div class="review" style="left:687px">
  <div class="stars">★★★★★</div>
  <p>“Perfect base for exploring Morvane. Quiet, comfortable, and incredibly well thought out...</p>
  <div class="who">Guest from Toronto</div>
</div>
<div class="review" style="left:975px">
  <div class="stars">★★★★★</div>
  <p>“Waking up to snow-covered trees and mountain views was magical. Truly a hidden gem...</p>
  <div class="who">Guest from Seattle</div>
</div>

<!-- FOOTER -->
<footer class="footer">
  <div class="brand-mark" style="left:185px;top:66px;width:64px;height:64px;border-color:#fff"></div>
  <div class="brand-name" style="left:92px;top:146px;width:250px;font-size:19px;color:#fff">Tollen Ridge<br>Canvas Camps</div>
  <div class="social" role="img" aria-label="Social profile link" style="left:151px;top:229px"></div>
  <div class="social" role="img" aria-label="Social profile link" style="left:186px;top:229px"></div>
  <div class="social" role="img" aria-label="Social profile link" style="left:221px;top:229px"></div>
  <div class="social" role="img" aria-label="Social profile link" style="left:256px;top:229px"></div>

  <h4 style="left:437px;top:42px">Explore</h4>
  <div class="uline" style="left:437px;top:85px"></div>
  <ul style="left:437px;top:103px"><li>Suites</li><li>About</li><li>Reviews</li><li>Explore Morvane</li><li>Contact</li></ul>

  <h4 style="left:667px;top:42px">Book</h4>
  <div class="uline" style="left:667px;top:85px"></div>
  <ul style="left:667px;top:103px"><li>Check Availability</li><li>Why Book Direct</li><li>Gift Stays</li></ul>

  <h4 style="left:919px;top:42px">Ready to Escape<br>the Crowds?</h4>
  <div class="uline" style="left:919px;top:120px"></div>
  <a class="btn btn-light" style="left:919px;top:156px;width:163px;height:34px;font-size:11px">Check Availability</a>

  <div class="copy">© 2026 Tollen Ridge Retreat. All rights reserved</div>
</footer>

</body>
</html>
```